Business card for builder specialising in renovations.

Need a card for our building business. Business name is under Martin Powles.
Have licence number on card ( 527691K)
Contact number (0400 382 415)
Want to work on logo for some business cards and shirts - something with MP or MPB or open to ideas??
No animations, No hammers. Something sharp and eye catching.
Highlight that we are a renovation specialist. Simple on front with extra details on back with some lines to jot down things.

Target Market(s)

Renovators

Industry/Entity Type

Building

Contact Information for Business Card

2 sided with room on back to jot things down.
Extra details on back so front can be simple ..like, renovations, bathrooms, decks, extensions, new builds,

Logo Text

MP

Font styles to use
Serif

Requirements
Must have
• Eye catching design .
• Name : Martin powles
• Licence number
• Contact number - 0400382415
Nice to have
• Some logo design that we can carry through to other forms of advertising
• Local builder
• Quality work
Should not have
• No animations

```html
<!DOCTYPE html>
<html lang="en">
<head>
<meta charset="utf-8">
<title>Martin Powles – Business Card</title>
<link rel="stylesheet" href="https://fonts.googleapis.com/css2?family=Libre+Baskerville:wght@400;700&display=swap">
<style>
  :root {
    --stage: #2a2a2b;
    --card: #050505;
    --ink: #ffffff;
    --brand-blue: #1677c4;
    --rule-blue: #1a6fb8;
    --muted: #d9d9d9;
  }
  * { margin: 0; padding: 0; box-sizing: border-box; }
  html, body {
    width: 1200px; height: 900px; overflow: hidden;
    background: var(--stage);
    font-family: "Libre Baskerville", "Times New Roman", serif;
  }
  .stage {
    width: 1200px; height: 900px;
    display: flex; flex-direction: column; align-items: center; justify-content: center;
    gap: 40px;
  }
  .card {
    position: relative; width: 700px; height: 400px;
    background: var(--card); border-radius: 22px; overflow: hidden;
    color: var(--ink);
  }
  .card-shapes { position: absolute; inset: 0; }

  .wordmark { position: absolute; display: flex; align-items: center; gap: 16px; }
  .wordmark-square { width: 18px; height: 18px; background: var(--brand-blue); flex: none; }
  .wordmark-name {
    font-weight: 400; color: var(--ink); text-transform: uppercase;
    line-height: 0.95; letter-spacing: 1px;
  }

  /* front */
  .card-front .wordmark { left: 205px; top: 120px; }
  .card-front .wordmark-name { font-size: 54px; }
  .services {
    position: absolute; left: 40px; top: 290px;
    font-size: 15px; letter-spacing: 0.5px; text-transform: uppercase;
    display: flex; align-items: center; gap: 10px; white-space: nowrap;
  }
  .services .dot { width: 8px; height: 8px; background: var(--brand-blue); }
  .front-web {
    position: absolute; left: 40px; top: 352px;
    font-size: 19px; color: var(--ink);
  }

  /* back */
  .card-back .wordmark { left: 45px; top: 62px; }
  .card-back .wordmark-name { font-size: 42px; }
  .holder { position: absolute; right: 40px; top: 150px; text-align: right; }
  .holder-name { font-size: 24px; color: var(--brand-blue); text-transform: uppercase; }
  .holder-role { font-size: 14px; color: var(--ink); margin-top: 2px; }
  .licence {
    position: absolute; right: 28px; top: 262px;
    font-size: 15px; color: var(--ink);
  }
  .contacts {
    position: absolute; left: 48px; top: 296px;
    list-style: none; font-size: 17px; line-height: 25px;
  }
  .contacts li { display: flex; align-items: center; gap: 12px; }
  .contacts svg { width: 14px; height: 14px; flex: none; }
  .contacts .accent { color: var(--brand-blue); }
</style>
</head>
<body>
<main class="stage">

  <section class="card card-front" aria-label="Card front">
    <svg class="card-shapes" viewBox="0 0 700 400" aria-hidden="true">
      <rect x="330" y="384" width="370" height="16" fill="var(--ink)"/>
      <polygon points="0,330 300,330 345,362 345,400 0,400" fill="var(--brand-blue)"/>
    </svg>
    <div class="wordmark">
      <span class="wordmark-square"></span>
      <span class="wordmark-name">Martin<br>Powles</span>
    </div>
    <p class="services">
      <span>Renovations</span><span class="dot"></span>
      <span>Bathrooms Decks</span><span class="dot"></span>
      <span>Extensions</span><span class="dot"></span>
      <span>New Builds</span>
    </p>
    <p class="front-web">www.martinpowles.com</p>
  </section>

  <section class="card card-back" aria-label="Card back">
    <svg class="card-shapes" viewBox="0 0 700 400" aria-hidden="true">
      <rect x="0" y="384" width="700" height="16" fill="var(--ink)"/>
      <polygon points="600,230 700,230 700,318 565,318" fill="var(--brand-blue)"/>
      <line x1="40" y1="286" x2="600" y2="196" stroke="var(--rule-blue)" stroke-width="2"/>
    </svg>
    <div class="wordmark">
      <span class="wordmark-square"></span>
      <span class="wordmark-name">Martin<br>Powles</span>
    </div>
    <div class="holder">
      <p class="holder-name">Martin Powles</p>
      <p class="holder-role">Director</p>
    </div>
    <p class="licence">Licence: (527691K)</p>
    <ul class="contacts">
      <li>
        <svg viewBox="0 0 24 24" aria-hidden="true"><path fill="var(--brand-blue)" d="M6.6 10.8a15 15 0 0 0 6.6 6.6l2.2-2.2c.3-.3.7-.4 1-.2 1.1.4 2.3.6 3.6.6.6 0 1 .4 1 1V20c0 .6-.4 1-1 1A17 17 0 0 1 3 4c0-.6.4-1 1-1h3.5c.6 0 1 .4 1 1 0 1.3.2 2.5.6 3.6.1.3 0 .7-.2 1z"/></svg>
        <span>0400382415</span>
      </li>
      <li>
        <svg viewBox="0 0 24 24" aria-hidden="true"><rect x="2" y="5" width="20" height="14" fill="none" stroke="var(--brand-blue)" stroke-width="2"/><path d="M2 5l10 8 10-8" fill="none" stroke="var(--brand-blue)" stroke-width="2"/></svg>
        <span>info@martinpowles.com</span>
      </li>
      <li>
        <svg viewBox="0 0 24 24" aria-hidden="true"><circle cx="12" cy="12" r="10" fill="none" stroke="var(--brand-blue)" stroke-width="2"/><path d="M2 12h20M12 2c3 3 3 17 0 20M12 2c-3 3-3 17 0 20" fill="none" stroke="var(--brand-blue)" stroke-width="2"/></svg>
        <span>www.<span class="accent">martinpowles</span>.com</span>
      </li>
    </ul>
  </section>

</main>
</body>
</html>
```